Moravel Aesthetic Doctor

I require an elegant, luxurious looking business card for my aesthetic business. I am a doctor and that will set me aside from competitors. I am planning to provide home and spa based treatments to clients with high expectations. I have attached my logo.

```html
<!DOCTYPE html>
<html lang="en">
<head>
<meta charset="utf-8">
<title>Moravel Aesthetic Doctor — Business Card</title>
<link href="https://fonts.googleapis.com/css2?family=Work+Sans:wght@300;400;500&display=swap" rel="stylesheet">
<style>
  :root {
    --backdrop: #161616;
    --card: #232323;
    --card-edge: #2c2c2c;
    --silver: #d6d6d6;
    --silver-soft: #a9a9a9;
    --silver-dim: #8a8a8a;
  }
  * { box-sizing: border-box; margin: 0; padding: 0; }
  html, body {
    width: 1200px; height: 900px; overflow: hidden;
    background: var(--backdrop);
    font-family: "Work Sans", sans-serif;
  }
  .stage {
    width: 1200px; height: 900px;
    display: flex; flex-direction: column; align-items: center; justify-content: center;
    gap: 40px;
  }
  .card {
    width: 640px; height: 366px;
    background: linear-gradient(135deg, var(--card) 0%, #1f1f1f 60%, #262626 100%);
    border: 1px solid var(--card-edge);
    border-radius: 3px;
    position: relative;
    color: var(--silver);
  }
  /* Front */
  .card-front {
    display: flex; flex-direction: column; align-items: center; justify-content: center;
    gap: 34px;
  }
  .brand { display: flex; align-items: center; gap: 18px; }
  .brand-dot {
    width: 64px; height: 64px; border-radius: 50%;
    border: 2px solid var(--silver-soft);
  }
  .brand-name {
    font-weight: 400; color: var(--silver);
    text-transform: uppercase; line-height: 1.05;
  }
  .brand-name .primary { display: block; font-size: 46px; letter-spacing: 3px; }
  .brand-name .secondary { display: block; font-size: 19px; letter-spacing: 2.5px; }
  .services {
    text-align: center; font-size: 15px; font-weight: 400;
    color: var(--silver-soft); letter-spacing: 1px; line-height: 1.45;
  }
  /* Back */
  .card-back { display: flex; flex-direction: column; align-items: center; }
  .details {
    display: flex; align-items: center; gap: 28px;
    margin-top: 104px;
  }
  .doctor { text-align: right; line-height: 1.3; }
  .doctor-name { font-size: 17px; font-weight: 500; color: var(--silver-soft); letter-spacing: 0.6px; }
  .doctor-credential { font-size: 15px; color: var(--silver-dim); letter-spacing: 0.8px; }
  .divider { width: 1px; height: 70px; background: var(--silver-dim); }
  .contact { list-style: none; font-size: 17px; letter-spacing: 1px; line-height: 1.5; color: var(--silver); }
  .contact li { display: flex; align-items: center; gap: 10px; }
  .contact svg { width: 12px; height: 12px; fill: none; stroke: var(--silver-soft); stroke-width: 1.6; }
  .tagline {
    position: absolute; bottom: 40px; left: 0; right: 0; text-align: center;
    font-size: 15px; letter-spacing: 2.5px; text-transform: uppercase; color: var(--silver-soft);
  }
</style>
</head>
<body>
<main class="stage">
  <section class="card card-front">
    <div class="brand">
      <span class="brand-dot"></span>
      <h1 class="brand-name">
        <span class="primary">Moravel</span>
        <span class="secondary">Aesthetic Doctor</span>
      </h1>
    </div>
    <p class="services">
      Dermal injectables | Plasma facials | Microneedling<br>
      Skin boosters | Excessive sweating
    </p>
  </section>

  <section class="card card-back">
    <div class="details">
      <div class="doctor">
        <p class="doctor-name">Dr Lena Varga MRCPCH MD</p>
        <p class="doctor-credential">Australasian Diploma<br>of Aesthetic Medicine</p>
      </div>
      <span class="divider"></span>
      <ul class="contact">
        <li>
          <svg viewBox="0 0 12 12" aria-hidden="true"><path d="M3 1 L4.6 3.6 L3.6 4.8 Q4.6 7 7.2 8.4 L8.4 7.4 L11 9 L10 11 Q4 10.6 1 2 Z"/></svg>
          0800 555 018
        </li>
        <li>
          <svg viewBox="0 0 12 12" aria-hidden="true"><rect x="1" y="2.5" width="10" height="7"/><path d="M1 2.5 L6 6.5 L11 2.5"/></svg>
          lena@moravel.co.nz
        </li>
        <li>
          <svg viewBox="0 0 12 12" aria-hidden="true"><circle cx="6" cy="6" r="5"/><ellipse cx="6" cy="6" rx="2.2" ry="5"/><path d="M1 6 H11"/></svg>
          www.moravel.co.nz
        </li>
      </ul>
    </div>
    <p class="tagline">Home and spa based treatments</p>
  </section>
</main>
</body>
</html>
```